We need a complete design for our construction company KELTO CONSTRUCTION based in Auckland New Zealand, we need a logo, website, business card, vehicle design etc..
We are a mid to high-end construction company who work mostly on residential projects and some commercial.

What we want to see in the design;
Professional,
Architectural,
Simple,
Alternative,

We want the design to communicate professionalism, high quality wormanship and and quality service.

Target Market(s)

People looking for a quality building/ construction company

Industry/Entity Type

Construction Company

Contact Information for Business Card

KELTO CONSTRUCTION.co.nz
Lino Verasek
lino@keltoconstruction.example.nz
021 5807 462

Logo Text

KELTO CONSTRUCTION

Number of Pages Required

5+ page

Font styles to use
Sans Serif

Colors

Designer to choose colors to be used in the design.

Requirements
Must have
• Must appear high end, professional, quality, be simple, easy to use, give security to potential clients
Nice to have
• high-quality photos of our recent projects
• about us page
• blog page
• contact us page
• high quality content
Should not have
• should not be hard to use and have too much going on.

```html
<!DOCTYPE html>
<html lang="en">
<head>
<meta charset="utf-8">
<title>Kelto Construction</title>
<link href="https://fonts.googleapis.com/css2?family=Raleway:wght@500;600;700;800&family=Open+Sans:ital,wght@0,400;0,600;0,700;1,400&display=swap" rel="stylesheet">
<style>
:root{
  --orange:#e0982a;
  --orange-dark:#d78a17;
  --ink:#1c1c1c;
  --text:#555;
  --grey-band:#8b8b90;
  --white:#fff;
  --black:#101010;
  --star:#c6cf1f;
}
*{box-sizing:border-box;margin:0;padding:0}
html,body{width:1200px;height:3309px;overflow:hidden;background:var(--white)}
body{font-family:"Open Sans",Arial,sans-serif;color:var(--text)}
.page{position:relative;width:1200px;height:3309px;overflow:hidden}
.abs{position:absolute}
h1,h2,h3,.nav,.brand{font-family:"Raleway",Arial,sans-serif}

/* hero */
.hero{left:0;top:0;width:1200px;height:600px}
.hero-photo{position:absolute;inset:0;background:linear-gradient(180deg,#8d97a2 0%,#a7a39a 35%,#6f6b62 62%,#5b6670 80%,#4e5a63 100%)}
.hero-shade{position:absolute;inset:0;background:rgba(20,20,20,.25)}
.hero-curve{position:absolute;left:0;top:0}
.brand{display:flex;align-items:center;gap:12px;color:var(--white);font-weight:800;font-size:25px;line-height:27px;letter-spacing:.3px}
.brand-mark{width:36px;height:36px;background:var(--white)}
.hero .brand{left:97px;top:38px}
.contact-bar{top:18px;right:95px;display:flex;gap:28px;color:var(--white);font-size:15px;align-items:center}
.contact-bar span{display:flex;align-items:center;gap:10px}
.ico-circle{width:30px;height:30px;border-radius:50%;border:2px solid var(--orange);display:flex;align-items:center;justify-content:center}
.nav{top:68px;right:95px;display:flex;gap:38px;color:var(--white);font-weight:700;font-size:15px;align-items:center}
.hero-title{top:186px;left:0;width:1200px;text-align:center;color:var(--white);font-weight:800;font-size:59px;letter-spacing:.5px}
.hero-sub{top:262px;left:0;width:1200px;text-align:center;color:var(--white);font-size:22px;font-weight:600}
.btn-outline{display:flex;align-items:center;justify-content:center;border:2px solid var(--white);border-radius:24px;color:var(--white);font-family:"Raleway",Arial,sans-serif;font-weight:700;font-size:15px}
.hero .btn-outline{left:523px;top:320px;width:154px;height:44px}
.dots{top:468px;left:0;width:1200px;display:flex;justify-content:center;gap:4px}
.dots i{width:13px;height:13px;border-radius:50%;border:2px solid var(--white)}
.dots i.on{background:var(--white)}

/* welcome */
.section-title{left:0;width:1200px;text-align:center;font-weight:700;font-size:35px;color:var(--ink)}
.lead{left:200px;width:800px;text-align:center;font-size:14.5px;line-height:30px}
.service{top:828px;width:170px;text-align:center}
.service .ring{width:166px;height:166px;margin:0 auto;border-radius:50%;border:2px solid #9a9a9a;display:flex;align-items:center;justify-content:center;background:var(--white)}
.service.active .ring{background:var(--orange);border:10px solid #f1c98a;box-shadow:0 0 0 2px var(--orange)}
.service p{margin-top:20px;font-family:"Raleway",Arial,sans-serif;font-weight:600;font-size:19px;line-height:25px;color:var(--ink)}

/* projects */
.projects{left:0;top:1143px;width:1200px;height:887px;background:var(--grey-band)}
.projects .section-title,.testimonials .section-title{color:var(--white)}
.projects .lead{color:#f3f3f3}
.tile{width:278px;height:245px;border:3px solid #e6e6e6}

/* blog */
.post{top:2176px;width:323px}
.post .thumb{height:184px}
.post h3{margin-top:26px;font-size:20px;font-weight:600;color:var(--ink)}
.meta{margin-top:10px;font-size:13px;display:flex;gap:8px;align-items:center}
.meta b{color:var(--orange)}
.post .excerpt{margin-top:14px;font-size:13px;line-height:23px}
.read-more{margin-top:14px;display:block;color:var(--orange-dark);font-weight:700;font-size:13px;font-family:"Raleway",Arial,sans-serif}

/* testimonials */
.testimonials{left:0;top:2610px;width:1200px;height:520px;background:var(--orange)}
.quote-card{top:2745px;width:320px;display:flex;gap:16px}
.avatar{flex:0 0 76px;height:76px;border-radius:50%;border:3px solid var(--white);background:linear-gradient(160deg,#d9cfc4,#8c7f74)}
.quote{color:var(--white);font-size:12.5px;font-style:italic;line-height:22px}
.quote .mark{font-family:Georgia,serif;font-size:26px;font-weight:700;font-style:normal;margin-right:6px;vertical-align:-8px}
.who{margin-top:16px;color:var(--white);font-size:10px;font-weight:700;text-transform:uppercase}
.role{color:var(--white);font-size:9.5px;font-style:italic}
.stars{top:2893px;font-size:22px;color:var(--star);letter-spacing:4px}
.arrow{width:38px;height:38px;border-radius:50%;border:2px solid var(--white);display:flex;align-items:center;justify-content:center;top:2800px}

/* footer */
.footer-curve{left:0;top:2960px}
.footer{left:0;top:3105px;width:1200px;height:204px;background:var(--black)}
.footer .brand{left:97px;top:3116px}
.legal{left:97px;color:var(--white);font-size:13px}
.f-col{top:3093px;color:var(--white)}
.f-col h4{font-family:"Raleway",Arial,sans-serif;font-size:18px;font-weight:700;margin-bottom:14px}
.f-col li{list-style:none;font-size:13px;line-height:21.5px}
.social{display:grid;grid-template-columns:44px 44px;gap:16px 16px}
.social span{width:44px;height:44px;border-radius:50%;border:2px solid var(--white)}
</style>
</head>
<body>
<div class="page">

  <!-- HERO -->
  <header class="abs hero">
    <div class="hero-photo" role="img" aria-label="City skyline across a harbour with a sailboat on the water"></div>
    <div class="hero-shade"></div>
    <svg class="hero-curve" width="1200" height="600" viewBox="0 0 1200 600" aria-hidden="true">
      <path d="M0 440 Q600 690 1200 440 L1200 430 Q600 655 0 430 Z" fill="#e0982a"/>
      <path d="M0 446 Q600 640 1200 446 L1200 600 L0 600 Z" fill="#e0982a"/>
      <path d="M0 452 Q600 620 1200 452 L1200 600 L0 600 Z" fill="#fff"/>
    </svg>
  </header>

  <div class="abs brand" style="left:97px;top:36px"><span class="brand-mark"></span><span>KELTO<br>CONSTRUCTION</span></div>
  <div class="abs contact-bar">
    <span><span class="ico-circle"><svg width="14" height="14" viewBox="0 0 24 24"><path d="M6.6 10.8a15 15 0 0 0 6.6 6.6l2.2-2.2a1 1 0 0 1 1-.25 11.4 11.4 0 0 0 3.6.6 1 1 0 0 1 1 1V20a1 1 0 0 1-1 1A17 17 0 0 1 3 4a1 1 0 0 1 1-1h3.5a1 1 0 0 1 1 1c0 1.25.2 2.45.57 3.57a1 1 0 0 1-.25 1z" fill="#e0982a"/></svg></span>1 800 555 0142</span>
    <span><span class="ico-circle"><svg width="14" height="12" viewBox="0 0 24 18"><rect x="1" y="1" width="22" height="16" rx="2" fill="#e0982a"/><path d="M2 2l10 8 10-8" stroke="#fff" stroke-width="2" fill="none"/></svg></span>info@keltoconstruction.example.com</span>
  </div>
  <nav class="abs nav">
    <span>HOME</span><span>ABOUT US</span><span>PROJECTS</span><span>BLOG</span><span>CONTACT US</span>
    <svg width="16" height="16" viewBox="0 0 24 24"><circle cx="10" cy="10" r="7" stroke="#fff" stroke-width="3" fill="none"/><path d="M15 15l6 6" stroke="#fff" stroke-width="3"/></svg>
  </nav>
  <h1 class="abs hero-title">KELTO CONSTRUCTION</h1>
  <p class="abs hero-sub">We are a construction company in Auckland, NewZealand</p>
  <a class="abs btn-outline" style="left:523px;top:320px;width:154px;height:44px">GET STARTED</a>
  <div class="abs dots"><i class="on"></i><i></i><i></i><i></i></div>

  <!-- WELCOME -->
  <h2 class="abs section-title" style="top:656px">WELCOME TO KELTO CONSTRUCTION</h2>
  <p class="abs lead" style="top:722px">Nam libero tempore, cum soluta nobis est eligendi optio cumque nihil impedit quo minus id quod maxime placeat facere possimus, omnis voluptas assumenda est, omnis dolor repellen autem quibusdam et aut officiis debiti</p>

  <div class="abs service" style="left:95px">
    <div class="ring"><svg width="70" height="60" viewBox="0 0 70 60"><g fill="#e0982a"><circle cx="35" cy="14" r="10"/><circle cx="15" cy="22" r="8"/><circle cx="55" cy="22" r="8"/><path d="M18 58c0-14 8-24 17-24s17 10 17 24z"/><path d="M2 54c0-10 6-18 13-18 3 0 5 1 7 3-4 5-6 10-6 15z"/><path d="M68 54c0-10-6-18-13-18-3 0-5 1-7 3 4 5 6 10 6 15z"/></g></svg></div>
    <p>Construction<br>Management</p>
  </div>
  <div class="abs service" style="left:305px">
    <div class="ring"><svg width="64" height="60" viewBox="0 0 64 60"><rect x="6" y="12" width="40" height="42" rx="6" fill="none" stroke="#e0982a" stroke-width="5"/><path d="M26 40l4-12 22-22 8 8-22 22z" fill="#e0982a"/></svg></div>
    <p>Preconstruction<br>Services</p>
  </div>
  <div class="abs service active" style="left:514px">
    <div class="ring"><svg width="54" height="64" viewBox="0 0 54 64"><path d="M4 2h32l16 16v44H4z" fill="#fff"/><path d="M36 2v16h16" fill="#f3c78a"/><g fill="#e0982a"><rect x="14" y="30" width="26" height="4"/><rect x="14" y="39" width="26" height="4"/><rect x="14" y="48" width="26" height="4"/></g></svg></div>
    <p>General<br>Contracting</p>
  </div>
  <div class="abs service" style="left:723px">
    <div class="ring"><svg width="66" height="60" viewBox="0 0 66 60"><g fill="#e0982a"><circle cx="24" cy="34" r="16"/><circle cx="50" cy="16" r="11"/><circle cx="50" cy="46" r="8"/></g><g fill="#fff"><circle cx="24" cy="34" r="6"/><circle cx="50" cy="16" r="4"/><circle cx="50" cy="46" r="3"/></g><g stroke="#e0982a" stroke-width="6"><path d="M24 13v42M3 34h42M9 19l30 30M39 19L9 49"/></g><circle cx="24" cy="34" r="6" fill="#fff"/></svg></div>
    <p>Design-Build<br>Services</p>
  </div>
  <div class="abs service" style="left:932px">
    <div class="ring"><svg width="56" height="56" viewBox="0 0 56 56"><path d="M46 22A19 19 0 0 0 12 16" stroke="#e0982a" stroke-width="7" fill="none"/><path d="M4 8l2 16 14-6z" fill="#e0982a"/><path d="M10 34a19 19 0 0 0 34 6" stroke="#e0982a" stroke-width="7" fill="none"/><path d="M52 48l-2-16-14 6z" fill="#e0982a"/></svg></div>
    <p>Remodeling<br>projects</p>
  </div>

  <!-- PROJECTS -->
  <section class="abs projects"></section>
  <h2 class="abs section-title" style="top:1203px">RECENT PROJECTS</h2>
  <p class="abs lead" style="top:1261px;color:#f3f3f3;font-size:14px;line-height:25px;left:220px;width:760px">Temporibus autem quibusdam et aut officiis debitis aut rerum necessitatibus saepe eveniet ut et voluptates repudian dae sint et molestiae non recusandae eaque earum rerum hic tenetur a sapiente</p>

  <div class="abs tile" style="left:18px;top:1356px;background:linear-gradient(180deg,#9fc4ea 0%,#c9d7e2 40%,#8a6a58 60%,#6a6e72 100%)" role="img" aria-label="Row of new brick townhouses along a street"></div>
  <div class="abs tile" style="left:313px;top:1356px;background:linear-gradient(180deg,#3f82d6 0%,#c7b79c 45%,#5f8a3c 75%,#4f8a2e 100%)" role="img" aria-label="Two-storey family home with a green lawn"></div>
  <div class="abs tile" style="left:608px;top:1356px;background:linear-gradient(180deg,#dfe9ee 0%,#7e8d6c 45%,#6a8f3e 75%,#b9b6ad 100%)" role="img" aria-label="Suburban house with driveway among trees"></div>
  <div class="abs tile" style="left:903px;top:1356px;background:linear-gradient(180deg,#2f6fd0 0%,#3e4a8a 35%,#d9a650 60%,#5e7c3e 85%,#8a6d55 100%)" role="img" aria-label="Modern apartment block with a landscaped courtyard"></div>
  <div class="abs tile" style="left:18px;top:1621px;background:linear-gradient(180deg,#cfe3f1 0%,#5b8a3c 35%,#6e5a4e 55%,#5a8f34 80%,#c9c7bf 100%)" role="img" aria-label="Brick bungalow behind a front lawn"></div>
  <div class="abs tile" style="left:313px;top:1621px;background:linear-gradient(180deg,#5e98d8 0%,#8090a4 40%,#6c6a6a 65%,#cfd0d2 100%)" role="img" aria-label="New homes along a residential street"></div>
  <div class="abs tile" style="left:608px;top:1621px;background:linear-gradient(180deg,#9bb3c7 0%,#e9e6df 40%,#c9b7a0 60%,#6b8a3e 100%)" role="img" aria-label="White multi-storey apartment building"></div>
  <div class="abs tile" style="left:903px;top:1621px;background:linear-gradient(180deg,#2b6fd6 0%,#5a93e4 45%,#8c9aa8 70%,#6a8c44 100%)" role="img" aria-label="Suburban neighbourhood of new houses"></div>

  <a class="abs btn-outline" style="left:494px;top:1910px;width:212px;height:48px">VIEW MORE PROJECTS</a>

  <!-- BLOG -->
  <h2 class="abs section-title" style="top:2098px">LATEST BLOG</h2>

  <article class="abs post" style="left:98px">
    <div class="thumb" style="background:linear-gradient(135deg,#dfe6ec 0%,#b7c3cf 50%,#e9c266 100%)" role="img" aria-label="Hands working over architectural plans on a desk"></div>
    <h3>Finibus Bonorum et Malorum</h3>
    <div class="meta"><b>&#9635;</b>25/09/2017 &nbsp;| <b>&#9679;</b>John</div>
    <p class="excerpt">Nemo enim ipsam voluptatem quia volupta asperna tur aut odit aut fugit, sed quia conseq.</p>
    <span class="read-more">READ MORE</span>
  </article>
  <article class="abs post" style="left:438px">
    <div class="thumb" style="background:linear-gradient(160deg,#3b86d8 0%,#8fb9e6 45%,#7d7f82 70%,#c99b3a 100%)" role="img" aria-label="Tower crane beside a high-rise under construction"></div>
    <h3>Finibus Bonorum et Malorum</h3>
    <div class="meta"><b>&#9635;</b>25/09/2017 &nbsp;| <b>&#9679;</b>John</div>
    <p class="excerpt">Nemo enim ipsam voluptatem quia volupta asperna tur aut odit aut fugit, sed quia conseq.</p>
    <span class="read-more">READ MORE</span>
  </article>
  <article class="abs post" style="left:778px">
    <div class="thumb" style="background:linear-gradient(90deg,#a0583a 0%,#c58a62 45%,#d9dd4a 75%,#9a5a3c 100%)" role="img" aria-label="Site worker in a hard hat in front of brickwork"></div>
    <h3>Finibus Bonorum et Malorum</h3>
    <div class="meta"><b>&#9635;</b>25/09/2017 &nbsp;| <b>&#9679;</b>John</div>
    <p class="excerpt">Nemo enim ipsam voluptatem quia volupta asperna tur aut odit aut fugit, sed quia conseq.</p>
    <span class="read-more">READ MORE</span>
  </article>

  <!-- TESTIMONIALS -->
  <section class="abs testimonials"></section>
  <h2 class="abs section-title" style="top:2668px">CLIENT TESTIMONIALS</h2>

  <div class="abs arrow" style="left:28px"><svg width="12" height="14" viewBox="0 0 12 14"><path d="M9 1L3 7l6 6" stroke="#fff" stroke-width="2.5" fill="none"/></svg></div>
  <div class="abs arrow" style="left:1132px"><svg width="12" height="14" viewBox="0 0 12 14"><path d="M3 1l6 6-6 6" stroke="#fff" stroke-width="2.5" fill="none"/></svg></div>

  <div class="abs quote-card" style="left:96px">
    <div class="avatar" role="img" aria-label="Client portrait"></div>
    <div><p class="quote"><span class="mark">&ldquo;</span>At vero eos et accusamus et iusto dignissimos ducimus qui blanditiipraesent ium voluptatum deleniti atq.</p>
    <p class="who">Marla Dennet</p><p class="role">Financial Services Professional</p></div>
  </div>
  <div class="abs quote-card" style="left:444px">
    <div class="avatar" role="img" aria-label="Client portrait"></div>
    <div><p class="quote"><span class="mark">&ldquo;</span>At vero eos et accusamus et iusto dignissimos ducimus qui blanditiipraesent ium voluptatum deleniti atqu.</p>
    <p class="who">Tobias R. Halvern</p><p class="role">National Urban Fellow at the Houston</p></div>
  </div>
  <div class="abs quote-card" style="left:791px">
    <div class="avatar" role="img" aria-label="Client portrait"></div>
    <div><p class="quote"><span class="mark">&ldquo;</span>At vero eos et accusamus et iusto dignissimos ducimus qui blanditiipraesent ium voluptatum deleniti atqu.</p>
    <p class="who">Iris Caldwen</p><p class="role">Creative Strategist | Entrepreneur &amp; Upcoming</p></div>
  </div>

  <div class="abs stars" style="left:186px">&#9733;&#9733;&#9733;&#9733;&#9734;</div>
  <div class="abs stars" style="left:536px">&#9733;&#9733;&#9733;&#9733;&#9733;</div>
  <div class="abs stars" style="left:883px">&#9733;&#9733;&#9733;&#9733;&#9734;</div>

  <!-- FOOTER -->
  <svg class="abs footer-curve" width="1200" height="150" viewBox="0 0 1200 150" aria-hidden="true">
    <path d="M0 128 Q600 -40 1200 128 L1200 150 L0 150 Z" fill="#fff"/>
    <path d="M0 142 Q600 -14 1200 142 L1200 150 L0 150 Z" fill="#101010"/>
  </svg>
  <footer class="abs footer"></footer>
  <div class="abs brand" style="left:97px;top:3116px"><span class="brand-mark"></span><span>KELTO<br>CONSTRUCTION</span></div>
  <p class="abs legal" style="top:3189px">Terms of Use - Privacy Policy</p>
  <p class="abs legal" style="top:3218px">Copyrights &copy; 2018, Kelto Construction.</p>

  <div class="abs f-col" style="left:461px"><h4>Information</h4>
    <ul><li>Home</li><li>About us</li><li>Projects</li><li>Blog</li><li>Contact us</li></ul></div>
  <div class="abs f-col" style="left:664px"><h4>Quick Links</h4>
    <ul><li>Help</li><li>FAQ</li><li>Support</li><li>Sitemap</li><li>Terms Of Use</li><li>Privacy Statement</li></ul></div>
  <div class="abs f-col" style="left:876px"><h4>Social Media</h4>
    <div class="social" aria-label="Social media links"><span></span><span></span><span></span><span></span></div></div>

</div>
</body>
</html>
```